Business Card Design needed for start up company Halvora

In need of a new business card designed for a start up company based in Sydney, Halvora is a new start up innovative Company, our mission it to make property accessible for everyday Australian and to become the leading Real Estate platform in Australia. We want it to be fresh and clean.

Industry/Entity Type

Financial

Contact Information for Business Card

Section for Name
Section for Title

HALVORA - The Strength of Pooling
Mobile:
Direct:

Font styles to use
Sans Serif

Colors
33a6d7
0692cd
0255a3
ffffff

Requirements
Must have
• Logo, all business card details

```html
<!DOCTYPE html>
<html lang="en">
<head>
<meta charset="utf-8">
<title>Halvora Business Card</title>
<link rel="stylesheet" href="https://fonts.googleapis.com/css2?family=Open+Sans:wght@400;600;700&display=swap">
<style>
  :root {
    --stage: #3b3d40;
    --card-dark: #1f2022;
    --card-dark-edge: #2c2d30;
    --card-light: #ffffff;
    --brand-sky: #33a6d7;
    --brand-blue: #0692cd;
    --brand-navy: #0255a3;
    --logo-grey: #d9d9d9;
    --text-grey: #6a6a6a;
    --rule: #0255a3;
  }
  * { margin: 0; padding: 0; box-sizing: border-box; }
  html, body {
    width: 1200px; height: 864px; overflow: hidden;
    background: var(--stage);
    font-family: "Open Sans", Arial, sans-serif;
  }
  .canvas {
    position: relative; width: 1200px; height: 864px;
    display: flex; flex-direction: column; align-items: center; justify-content: center; gap: 48px;
  }
  .card {
    width: 560px; height: 320px; border-radius: 4px; position: relative;
    box-shadow: 0 10px 30px rgba(0,0,0,.35);
  }
  .card--front {
    background: radial-gradient(ellipse at 55% 35%, var(--card-dark-edge), var(--card-dark) 70%);
    display: flex; flex-direction: column; align-items: center; justify-content: center;
  }
  .brand { display: flex; align-items: center; gap: 14px; }
  .brand__dot { border-radius: 50%; flex: none; }
  .brand__name { font-weight: 700; letter-spacing: 1px; line-height: 1; white-space: nowrap; }
  .card--front .brand__dot { background: var(--logo-grey); width: 64px; height: 64px; }
  .card--front .brand__name { color: var(--logo-grey); font-size: 58px; }
  .tagline {
    margin-top: 62px; color: #f2f2f2; font-size: 15px; letter-spacing: .3px;
  }
  .card--back { background: var(--card-light); display: flex; align-items: center; }
  .card--back .brand {
    width: 290px; flex: none; justify-content: center; gap: 10px;
    padding: 0 20px 0 30px; margin-top: 20px;
  }
  .card--back .brand__dot { background: var(--brand-blue); width: 44px; height: 44px; }
  .card--back .brand__name { color: var(--brand-navy); font-size: 32px; letter-spacing: .5px; }
  .divider { width: 2px; height: 196px; background: var(--rule); flex: none; }
  .details { padding-left: 22px; color: var(--text-grey); font-size: 13px; line-height: 1.45; }
  .details__name { color: var(--brand-navy); font-weight: 700; font-size: 20px; line-height: 1.1; }
  .details__title { font-size: 13px; margin-bottom: 14px; }
  .details__address { margin-bottom: 12px; }
  .contact { list-style: none; }
  .contact li { display: flex; align-items: center; gap: 8px; font-size: 15px; line-height: 1.35; white-space: nowrap; }
  .contact svg { width: 12px; height: 12px; flex: none; }
</style>
</head>
<body>
<main class="canvas">
  <section class="card card--front">
    <div class="brand">
      <span class="brand__dot"></span>
      <span class="brand__name">HALVORA</span>
    </div>
    <p class="tagline">The Strength of Pooling</p>
  </section>

  <section class="card card--back">
    <div class="brand">
      <span class="brand__dot"></span>
      <span class="brand__name">HALVORA</span>
    </div>
    <div class="divider"></div>
    <div class="details">
      <p class="details__name">Marcus Reed</p>
      <p class="details__title">President</p>
      <p class="details__address">Street Name Ave, Suite 000<br>State, Zip Code, Country</p>
      <ul class="contact">
        <li><svg viewBox="0 0 12 12"><path d="M2.5 1 L4.5 1 L5.3 3.5 L4 4.5 Q5 7 7.5 8 L8.5 6.7 L11 7.5 L11 9.5 Q11 11 9.5 11 Q1 10 1 2.5 Q1 1 2.5 1Z" fill="var(--brand-blue)"/></svg>02 9555-0147</li>
        <li><svg viewBox="0 0 12 12"><rect x="3" y="0.5" width="6" height="11" rx="1" fill="none" stroke="var(--brand-blue)" stroke-width="1.2"/><circle cx="6" cy="9.5" r=".8" fill="var(--brand-blue)"/></svg>0491 570 156</li>
        <li><svg viewBox="0 0 12 12"><rect x="0.5" y="2.5" width="11" height="7" fill="none" stroke="var(--brand-blue)" stroke-width="1.2"/><path d="M0.5 2.5 L6 7 L11.5 2.5" fill="none" stroke="var(--brand-blue)" stroke-width="1.2"/></svg>info@halvora.com.au</li>
        <li><svg viewBox="0 0 12 12"><circle cx="6" cy="6" r="5.2" fill="none" stroke="var(--brand-blue)" stroke-width="1.1"/><ellipse cx="6" cy="6" rx="2.3" ry="5.2" fill="none" stroke="var(--brand-blue)" stroke-width="1"/><path d="M1 6 H11" stroke="var(--brand-blue)" stroke-width="1"/></svg>halvora.com.au</li>
      </ul>
    </div>
  </section>
</main>
</body>
</html>
```